New webpage for Facility Management Company (cleaning services)

We need a new web page design for a company based in Stockholm, Sweden, called KBT Clean AB (established 1991). We provide cleaning services to the public sector, to businesses, and to home owners. Our services primarily include daily cleaning, floor care, window cleaning, and carpet cleaning.

Our company holds certificates for ISO 9001, ISO 14001, ISO 45001 and "Vitmossan".

Referring to "the Swedish model" we honor collective agreements between Fortiva (employer-representative organisation and relevant labour unions (e.g. Tjänstebund).
The final design should communicate that we are a trustworthy company with a well trained staff, high quality services combined with a commitment to run a sustainable business from a labour and environmental perspective.

DETAILS
General
-----------------------------------------------
• Language: Swedish (we provide text)
• Very important: Easy to administrate for company staff without special technical skills, especially to
o add/change information about HQ staff
o change any text
o add/change information about offered services
• Responsive
• SEO-friendly

Content that web page needs to cover in one way or the other
--------------------------------------------
• Information about our company
• About our staff and contact info to HQstaff/management (photos, contact info)
• Our ambitions and supporting info (quality, environment, labour conditions, certificates, etc)
• Information to customers within the public sector
• Information to customers within the private sector
• Information to customers within the home owner sector
• Services public sector (Swedish = Offentlig sektor)
• Services private business sector (Swedish = Företag) Se hellgren
• Services home owner sector (Swedish=Privat)
• GDPR compliance
• News

Content/Function
-------------------------------
• One specific requirement is that we need a page for information to potentially new employees (some general information and open job positions) with a possibility to fill in a simple application form and upload CV.(Mail?) CAPTCHA or equivalent.
• Contact form for customers with CAPTCHA or equivalent.
• Cookie management
• Integration social media (future); easy to manage/add/delete integration of social media.

We are not interested in a blog at this point of time

```html
<!DOCTYPE html>
<html lang="en">
<head>
<meta charset="utf-8">
<title>KBT Clean AB – Facility Management Company</title>
<link rel="stylesheet" href="https://fonts.googleapis.com/css2?family=Lato:wght@400;700&family=Playfair+Display:wght@400;700&display=swap">
<style>
:root{
  --blue:#0a8fd9;
  --blue-btn:#0b8ad6;
  --navy:#0b2a45;
  --ocean:#0d659c;
  --green:#53b84a;
  --forest:#1f5a44;
  --ink:#1d1d1d;
  --muted:#555;
  --light:#f3f5f7;
  --field:#efefef;
  --footer:#1c2128;
  --serif:'Playfair Display',serif;
  --sans:'Lato',sans-serif;
}
*{box-sizing:border-box;margin:0;padding:0}
html,body{width:1200px;height:4127px;overflow:hidden}
body{font-family:var(--sans);color:var(--ink);background:#fff;position:relative}
.abs{position:absolute}
.btn{display:inline-block;background:var(--blue-btn);color:#fff;font:700 11px var(--sans);letter-spacing:.3px;text-transform:uppercase;text-align:center}
.eyebrow{font:400 12px var(--sans);text-transform:uppercase;letter-spacing:.4px}
.photo{position:absolute}

/* top bar */
.topbar{top:0;left:0;width:1200px;height:17px;background:var(--blue);color:#fff;font:700 7px var(--sans)}
.topbar .left{left:130px;top:4px;text-transform:uppercase}
.topbar .right{right:135px;top:4px;text-transform:uppercase;letter-spacing:.3px}

/* header */
.header{top:17px;left:0;width:1200px;height:78px;background:#fff}
.brand-name{font:700 24px var(--sans);color:var(--navy);letter-spacing:.2px}
.header .brand-name{position:absolute;left:130px;top:26px}
.contact-item{position:absolute;top:26px;display:flex;gap:10px;align-items:center}
.contact-item small{display:block;font:400 7px var(--sans);color:var(--muted);text-transform:uppercase}
.contact-item span{font:400 10px var(--sans);color:var(--ink)}

/* hero */
.hero{top:95px;left:0;width:1200px;height:506px;overflow:hidden;background:linear-gradient(100deg,#0a2540 0%,#163852 45%,#3a5a6e 70%,#1d3b55 100%)}
.nav{position:absolute;top:0;left:130px;width:940px;height:38px;display:flex;align-items:center;font:400 11px var(--sans);color:#fff;text-transform:uppercase}
.nav a{color:#fff;text-decoration:none;margin-right:42px}
.nav .active{background:var(--green);height:38px;line-height:38px;padding:0 38px;clip-path:polygon(22px 0,100% 0,100% 100%,0 100%);margin-right:36px}
.nav .jobs{position:absolute;right:0;top:0;background:var(--green);height:38px;line-height:38px;padding:0 34px 0 18px;clip-path:polygon(0 0,100% 0,calc(100% - 22px) 100%,0 100%);margin:0}
.hero-text{position:absolute;left:130px;top:137px;color:#fff}
.hero-text h1{font:700 38px/48px var(--serif);margin-top:8px}
.hero-text p{font:400 12.5px/20px var(--sans);margin-top:12px;width:300px}
.hero-text .btn{margin-top:22px;width:112px;height:34px;line-height:34px}

/* welcome */
.welcome-photo{left:130px;top:679px;width:460px;height:442px;background:linear-gradient(135deg,#2b8ca4,#c9c2b8 55%,#e6cf3a);clip-path:polygon(20% 0,100% 0,100% 85%,88% 100%,0 100%,0 23%)}
.welcome-text{left:690px;top:727px;width:385px}
.welcome-text h2{font:400 33px var(--serif);margin-top:6px}
.welcome-text p.lead{font:400 12px/20px var(--sans);margin-top:26px}
.welcome-mini{left:690px;top:900px;width:130px;height:112px;background:linear-gradient(135deg,#cfd6dc,#2e3c4a)}
.welcome-list{left:838px;top:910px;width:235px;list-style:none;font:400 8.3px/12px var(--sans);color:var(--muted)}
.welcome-list li{position:relative;padding-left:11px;margin-bottom:8px}
.welcome-list li::before{content:"";position:absolute;left:0;top:3px;width:5px;height:5px;border-radius:50%;background:var(--green)}
.welcome-btn{left:690px;top:1037px;width:112px;height:34px;line-height:34px}

/* services */
.services{top:1202px;left:0;width:1200px;height:557px;background:var(--ocean);color:#fff}
.center{text-align:center;width:100%;position:absolute;left:0}
.services .head{top:56px}
.services h2,.premises h2,.team h2{font:400 35px var(--serif);margin-top:6px}
.services .sub{font:400 12px var(--sans);margin-top:12px}
.svc-card{position:absolute;top:169px;width:300px;height:330px;background:var(--ocean);border:1px solid rgba(255,255,255,.18);text-align:center}
.svc-card .photo{left:0;top:0;width:300px;height:200px}
.svc-card .arch{position:absolute;left:60px;top:172px;width:180px;height:60px;background:var(--ocean);border-radius:90px 90px 0 0}
.svc-card h3{position:absolute;top:183px;width:100%;font:400 18px var(--serif)}
.svc-card p{position:absolute;top:226px;left:25px;width:250px;font:400 10.5px/16px var(--sans);opacity:.9}
.svc-card .btn{position:absolute;left:94px;top:277px;width:112px;height:34px;line-height:34px}

/* premises */
.premises{top:1759px;left:0;width:1200px;height:471px;background:var(--light)}
.premises .head{top:62px;color:var(--ink)}
.prem-card{position:absolute;top:144px;width:300px;height:261px;background:#fff;box-shadow:0 2px 6px rgba(0,0,0,.06)}
.prem-card .photo{left:0;top:0;width:300px;height:220px}
.prem-card h3{position:absolute;left:16px;top:228px;font:400 16px var(--serif)}
.prem-card .icon{position:absolute;right:0;top:220px;width:48px;height:41px;background:var(--green)}
.arrow-btn{position:absolute;top:223px;width:40px;height:40px;border:1px solid #cfd3d7;border-radius:50%;background:#fff}

/* team */
.team{top:2230px;left:0;width:1200px;height:583px}
.team .head{top:82px}
.member{position:absolute;top:157px;width:300px;height:346px}
.member .photo{left:32px;top:0;width:236px;height:240px;background:linear-gradient(180deg,#e3f1f9,#c8dfeb)}
.member .base{position:absolute;left:0;top:220px;width:300px;height:126px;background:var(--blue)}
.member svg.curve{position:absolute;left:0;top:196px}
.member h3{position:absolute;top:262px;width:100%;text-align:center;font:700 18px var(--serif);color:#fff}
.member .role{position:absolute;top:292px;width:100%;text-align:center;font:400 11px var(--sans);color:#fff}
.member.featured .photo{background:linear-gradient(180deg,#3aa7e0,#1790d3)}
.member.featured .base{background:#fff;border:1px solid #e3e3e3;top:227px;height:119px;border-top:3px solid var(--blue)}
.member.featured h3{color:var(--ink);top:237px}
.member.featured .role{color:var(--ink);top:269px}
.member .meta{position:absolute;top:312px;left:10px;right:16px;display:flex;justify-content:space-between;font:400 7px var(--sans);color:var(--ink);border-top:1px solid #e3e3e3;padding-top:9px}

/* news */
.news{top:2813px;left:256px;width:944px;height:338px;background:radial-gradient(ellipse at 40% 40%,#2b6a50,var(--forest) 70%)}
.news-person{left:130px;top:2800px;width:190px;height:351px;background:linear-gradient(180deg,#d9c6b2,#8fc7c0 50%,#6fb3b0)}
.news .head{position:absolute;left:115px;top:45px;color:#fff}
.news .head h2{font:400 35px var(--serif);margin-top:4px}
.post{position:absolute;display:flex;gap:14px;color:#fff}
.post .thumb{width:126px;height:85px;border:3px solid #fff;background:linear-gradient(135deg,#d9dee3,#5f7486)}
.post small{display:block;font:400 8px var(--sans);margin-top:10px;text-transform:uppercase}
.post h4{font:400 14px/21px var(--serif);width:200px;margin-top:6px}

/* contact */
.contact-head{left:130px;top:3228px}
.contact-head h2{font:400 35px/40px var(--serif);margin-top:6px}
.field{position:absolute;background:var(--field);font:400 10px var(--sans);color:#333;padding:20px 0 0 22px}
.submit{left:130px;top:3619px;width:139px;height:45px;line-height:45px}
.contact-photo{left:830px;top:3230px;width:370px;height:436px;background:linear-gradient(135deg,#d9e1d4,#f0f0ec 45%,#2a4a6a 75%,#e1c02c);clip-path:polygon(18% 0,100% 0,100% 100%,0 100%,0 26%)}

/* footer */
.footer{top:3745px;left:0;width:1200px;height:382px;background:var(--footer);color:#fff}
.footer .brand-name{position:absolute;left:130px;top:68px;color:#fff;font-size:26px}
.footer .about{position:absolute;left:130px;top:140px;width:230px;font:400 11px/17px var(--sans)}
.social{position:absolute;left:130px;top:200px;display:flex;gap:11px}
.social span{width:29px;height:29px;border-radius:50%;background:var(--green)}
.fcol{position:absolute;top:67px}
.fcol h4{font:400 16px var(--serif);color:var(--green);margin-bottom:22px}
.fcol li{list-style:none;font:400 11px var(--sans);margin-bottom:12px}
.fcontact{display:flex;gap:12px;align-items:center;margin-bottom:18px;font:400 11px/15px var(--sans)}
.fcontact i{flex:none;width:29px;height:29px;border-radius:50%;border:1px solid #555;display:flex;align-items:center;justify-content:center}
.footer .rule{position:absolute;left:130px;top:274px;width:940px;height:1px;background:#2d333b}
.copy{position:absolute;left:130px;top:303px;font:400 9px var(--sans);color:#8a8f96}
.copy b{font-weight:400;color:var(--blue)}
.cert{position:absolute;right:130px;top:298px;display:flex;gap:10px;align-items:center;font:400 11px var(--sans);text-decoration:underline}
.cert span{width:22px;height:22px;border-radius:50%;background:#cfd3d7}
</style>
</head>
<body>

<div class="abs topbar">
  <div class="abs left">We have more than 30 years of experiences</div>
  <div class="abs right">Sitemap &nbsp;|&nbsp; Quick link &nbsp;|&nbsp; &#x2315;</div>
</div>

<header class="abs header">
  <div class="brand-name">KBT Clean AB</div>
  <div class="contact-item" style="left:606px">
    <svg width="16" height="20" viewBox="0 0 16 20" fill="none" stroke="#333" stroke-width="1.3"><path d="M8 19s6-6.5 6-11A6 6 0 0 0 2 8c0 4.5 6 11 6 11z"/><circle cx="8" cy="8" r="2.2"/></svg>
    <div><small>Find us</small><span>Lindvägen 12, 117 43 Stockholm</span></div>
  </div>
  <div class="contact-item" style="left:836px">
    <svg width="12" height="20" viewBox="0 0 12 20" fill="none" stroke="#333" stroke-width="1.3"><rect x="1" y="1" width="10" height="18" rx="2"/><line x1="5" y1="16" x2="7" y2="16"/></svg>
    <div><small>Call us today</small><span>08-512 30 40</span></div>
  </div>
  <div class="contact-item" style="left:956px">
    <svg width="18" height="16" viewBox="0 0 18 16" fill="none" stroke="#333" stroke-width="1.3"><rect x="1" y="4" width="16" height="11"/><path d="M1 4l8 6 8-6M4 4V1h10v3"/></svg>
    <div><small>Email us</small><span>info@kbtclean.se</span></div>
  </div>
</header>

<section class="abs hero">
  <div class="photo" role="img" aria-label="Cleaner in gloves mopping a floor with colleagues in an office, framed in a drop shape" style="left:460px;top:40px;width:300px;height:440px;border-radius:50% 50% 45% 45%/30% 30% 70% 70%;background:linear-gradient(180deg,#6e8796,#9fb2bb 50%,#2f4d62)"></div>
  <svg class="abs" style="left:0;top:330px" width="1200" height="176" viewBox="0 0 1200 176"><path d="M0 40 C200 30 320 90 520 150 C650 185 900 150 1200 60 L1200 176 L0 176 Z" fill="#0a6ea8" opacity=".9"/></svg>
  <nav class="nav">
    <a class="active">Home</a><a>About us</a><a>Services</a><a>News</a><a>Contact us</a>
    <a class="jobs">Search for jobs</a>
  </nav>
  <div class="hero-text">
    <div class="eyebrow">Cleaning services</div>
    <h1>Facility Management<br>Company</h1>
    <p>The cleaning company where quality is always higher than price! We have 30 years of experience!</p>
    <a class="btn">Contact us</a>
  </div>
</section>

<div class="abs welcome-photo" role="img" aria-label="Cleaner in blue overalls mopping a living room with a yellow sofa"></div>
<svg class="abs" style="left:480px;top:950px" width="120" height="150" viewBox="0 0 120 150" fill="none" stroke="#1a8fd6" stroke-width="2"><circle cx="57" cy="106" r="40"/><circle cx="60" cy="40" r="11"/><circle cx="30" cy="143" r="10"/><circle cx="78" cy="17" r="6" fill="#1a8fd6" stroke="none"/><circle cx="10" cy="116" r="6" fill="#1a8fd6" stroke="none"/></svg>
<div class="abs welcome-text">
  <div class="eyebrow">Welcome to</div>
  <h2>KBT Cleaning AB</h2>
  <p class="lead">The cleaning company where quality is always higher than price! We have 30 years of experience! We have very satisfied customers according to our customer surveys!</p>
</div>
<div class="abs welcome-mini" role="img" aria-label="Cleaner wiping a table"></div>
<ul class="abs welcome-list">
  <li>KBT Clean is a cleaning company with cleaning of schools, offices, stairs, apartments etc.</li>
  <li>We also perform floor care, major cleaning, window cleaning, major cleaning, moving cleaning, etc.</li>
  <li>KBT Clean has extensive experience with great competence. We have approximately 250 employees.</li>
</ul>
<a class="abs btn welcome-btn">Read more</a>

<section class="abs services">
  <div class="center head">
    <div class="eyebrow">We offering</div>
    <h2>Our Services</h2>
    <div class="sub">KBT Clean AB works with premises cleaning and related services.</div>
  </div>
  <article class="svc-card" style="left:130px">
    <div class="photo" role="img" aria-label="Cleaners working in an office" style="background:linear-gradient(135deg,#e9ece8,#b4b8b0)"></div>
    <div class="arch"></div><h3>Public Sector</h3>
    <p>Sed ut perspiciatis unde omnis iste natus error sit voluptatem accusantium...</p>
    <a class="btn">Read more</a>
  </article>
  <article class="svc-card" style="left:450px">
    <div class="photo" role="img" aria-label="Worker cleaning a carpet with a machine" style="background:linear-gradient(135deg,#dfe2e4,#7d8790)"></div>
    <div class="arch"></div><h3>Businesses Sector</h3>
    <p>Sed ut perspiciatis unde omnis iste natus error sit voluptatem accusantium...</p>
    <a class="btn">Read more</a>
  </article>
  <article class="svc-card" style="left:770px">
    <div class="photo" role="img" aria-label="Cleaner vacuuming a sofa in a home" style="background:linear-gradient(135deg,#cfd7de,#2c7cc0)"></div>
    <div class="arch"></div><h3>Home Owner</h3>
    <p>Sed ut perspiciatis unde omnis iste natus error sit voluptatem accusantium...</p>
    <a class="btn">Read more</a>
  </article>
</section>

<section class="abs premises">
  <div class="center head">
    <div class="eyebrow">What we do</div>
    <h2>The Premises Maintenance Includes</h2>
  </div>
  <svg class="arrow-btn" style="left:45px" viewBox="0 0 40 40"><path d="M22 16l-4 4 4 4" stroke="#333" stroke-width="1.4" fill="none"/></svg>
  <svg class="arrow-btn" style="left:1115px" viewBox="0 0 40 40"><path d="M18 16l4 4-4 4" stroke="#333" stroke-width="1.4" fill="none"/></svg>
  <article class="prem-card" style="left:130px">
    <div class="photo" role="img" aria-label="Cleaner vacuuming a sofa" style="background:linear-gradient(135deg,#eef0ee,#b9b3a6)"></div>
    <h3>Daly Cleaning</h3><div class="icon"></div>
  </article>
  <article class="prem-card" style="left:450px">
    <div class="photo" role="img" aria-label="Worker cleaning an office floor with a machine" style="background:linear-gradient(135deg,#e3e8ec,#8a939a)"></div>
    <h3>Floor Cleaning</h3><div class="icon"></div>
  </article>
  <article class="prem-card" style="left:770px">
    <div class="photo" role="img" aria-label="Cleaner spraying a window" style="background:linear-gradient(135deg,#3a3330,#a49b93)"></div>
    <h3>Window Cleaning</h3><div class="icon"></div>
  </article>
</section>

<section class="abs team">
  <div class="center head">
    <div class="eyebrow">Current member</div>
    <h2>Meet Our Team</h2>
  </div>
  <div class="member" style="left:130px">
    <div class="photo" role="img" aria-label="Portrait of the CEO"></div>
    <svg class="curve" width="300" height="30" viewBox="0 0 300 30"><path d="M0 0 Q150 60 300 0 V30 H0Z" fill="#0a8fd9"/></svg>
    <div class="base"></div>
    <h3>Henrik Lindqvist</h3><div class="role">CEO</div>
  </div>
  <div class="member featured" style="left:450px">
    <div class="photo" role="img" aria-label="Portrait of the finance and purchasing manager"></div>
    <div class="base"></div>
    <h3>Maria Sandberg</h3><div class="role">Finance &amp; purchasing</div>
    <div class="meta"><span>30 YEARS EXPERIENCE</span><span>Mob: 08 – 512 30 45</span></div>
  </div>
  <div class="member" style="left:770px">
    <div class="photo" role="img" aria-label="Portrait of the supervisor"></div>
    <svg class="curve" width="300" height="30" viewBox="0 0 300 30"><path d="M0 0 Q150 60 300 0 V30 H0Z" fill="#0a8fd9"/></svg>
    <div class="base"></div>
    <h3>Sara Holmgren</h3><div class="role">Supervisor</div>
  </div>
</section>

<section class="abs news">
  <div class="head">
    <div class="eyebrow">Latest post</div>
    <h2>Recent News</h2>
  </div>
  <div class="post" style="left:484px;top:48px"><div class="thumb" role="img" aria-label="Cleaners in an office"></div><div><small>Excepteur sint</small><h4>Occaecat Cupidatat non amet Proident</h4></div></div>
  <div class="post" style="left:115px;top:176px"><div class="thumb" role="img" aria-label="Cleaner at work"></div><div><small>Excepteur sint</small><h4>Occaecat Cupidatat non amet Proident</h4></div></div>
  <div class="post" style="left:484px;top:176px"><div class="thumb" role="img" aria-label="Window cleaning"></div><div><small>Excepteur sint</small><h4>Occaecat Cupidatat non amet Proident</h4></div></div>
</section>
<div class="abs news-person" role="img" aria-label="Smiling cleaner in an apron holding a mop and spray bottle"></div>

<div class="abs contact-head">
  <div class="eyebrow">Contact us</div>
  <h2>If You Have Any<br>Question?</h2>
</div>
<div class="field" style="left:130px;top:3357px;width:300px;height:59px">First Name:</div>
<div class="field" style="left:439px;top:3357px;width:300px;height:59px">Last Name:</div>
<div class="field" style="left:130px;top:3425px;width:300px;height:59px">Email:</div>
<div class="field" style="left:439px;top:3425px;width:300px;height:59px">Phone:</div>
<div class="field" style="left:130px;top:3493px;width:609px;height:113px">Message:</div>
<a class="abs btn submit">Submit</a>
<div class="abs contact-photo" role="img" aria-label="Cleaner in yellow gloves wiping a window frame"></div>
<svg class="abs" style="left:770px;top:3470px" width="130" height="140" viewBox="0 0 130 140" fill="none" stroke="#1a8fd6" stroke-width="2"><circle cx="76" cy="80" r="40"/><circle cx="65" cy="18" r="12"/><circle cx="33" cy="130" r="10"/><circle cx="84" cy="7" r="6" fill="#1a8fd6" stroke="none"/><circle cx="15" cy="100" r="6" fill="#1a8fd6" stroke="none"/></svg>

<footer class="abs footer">
  <div class="brand-name">KBT Clean AB</div>
  <p class="about">The cleaning company where quality is always higher than price! We have 30 years of experience!</p>
  <div class="social"><span></span><span></span><span></span></div>
  <div class="fcol" style="left:463px"><h4>Quick Links</h4><ul><li>Home</li><li>About Us</li><li>Services</li><li>News</li><li>Contact Us</li></ul></div>
  <div class="fcol" style="left:668px"><h4>What We Do</h4><ul><li>Daily Cleaning</li><li>Floor Care</li><li>Window Cleaning</li><li>Carpet Cleaning</li></ul></div>
  <div class="fcol" style="left:876px;width:200px"><h4>Contact Us</h4>
    <div class="fcontact"><i><svg width="10" height="13" viewBox="0 0 16 20" fill="none" stroke="#53b84a" stroke-width="2"><path d="M8 19s6-6.5 6-11A6 6 0 0 0 2 8c0 4.5 6 11 6 11z"/></svg></i>Lindvägen 12, 117 43<br>Stockholm, Sweden</div>
    <div class="fcontact"><i><svg width="11" height="11" viewBox="0 0 12 12" fill="none" stroke="#53b84a" stroke-width="1.5"><path d="M2 1l2.5 0 1 3-1.5 1a7 7 0 0 0 3 3l1-1.5 3 1V10a1 1 0 0 1-1 1A9 9 0 0 1 1 2a1 1 0 0 1 1-1z"/></svg></i>08-512 30 40</div>
    <div class="fcontact"><i><svg width="12" height="10" viewBox="0 0 18 16" fill="none" stroke="#53b84a" stroke-width="2"><rect x="1" y="3" width="16" height="12"/><path d="M1 3l8 6 8-6"/></svg></i>info@kbtclean.se</div>
  </div>
  <div class="rule"></div>
  <div class="copy">Copyright © 2022 <b>KBT Clean AB</b>. All Rights Reserved.</div>
  <div class="cert"><span></span>ISO 9001, ISO 14001, ISO 45001</div>
</footer>

</body>
</html>
```